Gulf Book About Father - need cover design named - الغيم

The book talks about the good father who teaches his sons high principles and values, to be successful people in their lives.

Book size - 15 cm high
21 cm width
Data on the cover:
Name of the Book: الغيم
Author: دكتور/ مازن بن وليد الحمداني- Just write the name without the word writer
1440-2018
Logo of the Publishing House

Target Market(s)

Book submitted to children - Families - Schools - Public libraries

Requirements
Must have
• Design must include one or all of these options:
• The first option: a picture that has a meaning for a father who has values and principles with the son or children, expresses the contradiction - education, etc. -
• The background is to express the tender love or taken from the Emirates flag
• The second option: abstract art - with a background taken from the colors of the flag of the Emirates - or colors about love and tenderness
Should not have
• direct image

```html
<!DOCTYPE html>
<html lang="ar" dir="rtl">
<head>
<meta charset="utf-8">
<title>الغيم — غلاف كتاب</title>
<link rel="stylesheet" href="https://fonts.googleapis.com/css2?family=Noto+Kufi+Arabic:wght@900&family=Lalezar&family=Cairo:wght@600;700&display=swap">
<style>
  :root {
    --cover-yellow: #ffc90c;
    --title-red: #b91f2e;
    --band-red: #c1352d;
    --band-text: #ffd21a;
    --strip-white: #ffffff;
    --photo-glow: #fdf3ee;
    --photo-light: #f4dcd4;
    --photo-mid: #e2b5a8;
    --photo-deep: #c48879;
    --skin-dark: #9c6b58;
    --skin-light: #e9b9a3;
    --logo-ink: #5a3216;
    --logo-accent: #c8601e;
  }
  * { margin: 0; padding: 0; box-sizing: border-box; }
  html, body { width: 938px; height: 1200px; overflow: hidden; background: var(--cover-yellow); }
  .cover { position: relative; width: 938px; height: 1200px; background: var(--cover-yellow); }

  .title-area {
    position: absolute; top: 0; left: 0; width: 938px; height: 534px;
    display: flex; align-items: center; justify-content: center;
  }
  .book-title {
    font-family: "Noto Kufi Arabic", "Cairo", sans-serif;
    font-weight: 900; font-size: 250px; line-height: 1.5;
    color: var(--title-red); margin-top: -10px;
  }

  .cover-photo {
    position: absolute; top: 534px; left: 0; width: 938px; height: 529px;
    background:
      linear-gradient(180deg, rgba(120,80,70,0.28) 0%, rgba(120,80,70,0) 5%),
      radial-gradient(ellipse 34% 40% at 16% 48%, rgba(156,107,88,0.75) 0%, rgba(156,107,88,0) 100%),
      radial-gradient(ellipse 22% 28% at 40% 64%, rgba(190,140,120,0.55) 0%, rgba(190,140,120,0) 100%),
      radial-gradient(ellipse 22% 34% at 66% 54%, rgba(233,185,163,0.7) 0%, rgba(233,185,163,0) 100%),
      radial-gradient(circle at 52% 56%, var(--photo-glow) 0%, rgba(253,243,238,0) 22%),
      radial-gradient(circle at 28% 82%, rgba(253,243,238,0.7) 0%, rgba(253,243,238,0) 10%),
      radial-gradient(circle at 84% 30%, rgba(253,243,238,0.6) 0%, rgba(253,243,238,0) 12%),
      radial-gradient(circle at 8% 80%, rgba(253,243,238,0.5) 0%, rgba(253,243,238,0) 9%),
      linear-gradient(100deg, var(--photo-mid) 0%, var(--photo-light) 35%, var(--photo-glow) 55%, var(--photo-light) 75%, var(--photo-deep) 100%);
  }

  .publisher-box {
    position: absolute; top: 907px; left: 708px; width: 177px; height: 156px;
    background: var(--strip-white);
    display: flex; flex-direction: column; align-items: center; justify-content: center; gap: 6px;
  }
  .publisher-mark { width: 46px; height: 46px; background: var(--logo-accent); }
  .publisher-name { font-family: "Cairo", sans-serif; font-weight: 700; font-size: 17px; line-height: 1.2; color: var(--logo-ink); }
  .publisher-tagline { font-family: "Cairo", sans-serif; font-weight: 700; font-size: 9px; line-height: 1; color: var(--logo-ink); }

  .white-strip { position: absolute; top: 1063px; left: 0; width: 938px; height: 12px; background: var(--strip-white); }

  .info-band {
    position: absolute; top: 1075px; left: 0; width: 938px; height: 83px;
    background: var(--band-red);
    display: flex; align-items: center; justify-content: space-between;
    padding: 0 86px 0 91px;
    font-family: "Lalezar", "Cairo", sans-serif; font-size: 40px; color: var(--band-text);
  }
  .author-name { line-height: 1; }
  .edition-year { line-height: 1; direction: ltr; unicode-bidi: isolate; }
</style>
</head>
<body>
  <main class="cover">
    <section class="title-area">
      <h1 class="book-title">الغَيْمُ</h1>
    </section>
    <div class="cover-photo" role="img" aria-label="صورة يد أب ويد طفل تشكلان معاً شكل قلب على خلفية وردية فاتحة مضيئة"></div>
    <div class="publisher-box">
      <span class="publisher-mark"></span>
      <span class="publisher-name">دار نخلة الساحل</span>
      <span class="publisher-tagline">للطباعة والنشر والتوزيع</span>
    </div>
    <div class="white-strip"></div>
    <footer class="info-band">
      <span class="author-name">مازن بن وليد الحمداني</span>
      <span class="edition-year">۱۴۴۰-۲۰۱۸</span>
    </footer>
  </main>
</body>
</html>
```